LoopVane - A ride hailing server VAR

our Brindle.co profile: https://brindle.co/517loopvane

LOOPVANE offers first world solutions to first world problems. These days, our smartphones are our cameras, our wallets and our ride home. LOOPVANE guarantees that even if your phone is lost or dies, you'll never get stranded again. Simply call or text (SMS) our toll-free number to request a ride, and choose from one of the various services you subscribe to. LOOPVANE verifies your identity through a unique pin, making it possible to request rides through your own account from a stranger's phone via text or phone call. You can also login through our website or our App, making it easier than ever to get home phoneless.

LOOPVANE is a heterogeneous ride-hailing service that allows users for request transportation from any "transportation network company," taxi, helicopter service, jet service or any transportation service company that is publicly available. LOOPVANE will allow users to connect through our site, automated phone system, App or any appropriated touch point available.

Target Market(s)

RIde Haling

Coding

Coded - Design and coding required

Number of Pages Required

4 page

Requirements
Must have
• hav
Nice to have
• e the same functionality as our competitor's site: https://hopquill.com/
Should not have
• should not be cheezy
• We need to have the registration/sign up on the main page like https://www.zarvix.com/

```html
<!DOCTYPE html>
<html lang="en">
<head>
<meta charset="utf-8">
<title>LoopVane – Ride hailing</title>
<link rel="stylesheet" href="https://fonts.googleapis.com/css2?family=Arvo:wght@400;700&family=Raleway:wght@400;500;700&display=swap">
<style>
  :root {
    --orange: #f9a20f;
    --orange-nav: #f7a10e;
    --ink: #2f2f2f;
    --brown: #3a2708;
    --sky: #b6e3f6;
    --sky-deep: #a3d3e4;
    --rule: #333333;
    --white: #ffffff;
  }
  * { box-sizing: border-box; margin: 0; padding: 0; }
  html, body { width: 1200px; height: 910px; overflow: hidden; background: var(--white); }
  body { position: relative; font-family: "Raleway", sans-serif; color: var(--ink); }

  .site-header { position: absolute; left: 0; top: 0; width: 1200px; height: 86px; }
  .brand { position: absolute; left: 132px; top: 10px; display: flex; align-items: center; }
  .brand-mark { width: 62px; height: 62px; background: var(--orange); border-radius: 4px; }
  .brand-name { margin-left: 20px; margin-top: 12px; font-family: "Arvo", serif; font-weight: 700; font-size: 29px; color: var(--brown); }
  .search-icon { position: absolute; left: 1050px; top: 14px; }
  .main-nav { position: absolute; top: 57px; right: 133px; display: flex; gap: 40px; list-style: none; }
  .main-nav a { font-size: 12px; color: var(--brown); text-decoration: none; }
  .main-nav a.is-active { color: var(--orange-nav); }

  .hero { position: absolute; left: 0; top: 86px; width: 1200px; height: 445px;
    background: linear-gradient(180deg, var(--sky) 0%, var(--sky) 40%, var(--sky-deep) 100%); }
  .hero-title { position: absolute; left: 0; right: 0; top: 54px; text-align: center;
    font-family: "Arvo", serif; font-weight: 700; font-size: 38px; color: var(--brown); }

  .intro { position: absolute; left: 120px; width: 960px; top: 572px; text-align: center;
    font-size: 19px; line-height: 35px; color: #333; text-transform: uppercase; }

  .steps { position: absolute; top: 691px; left: 0; width: 1200px; }
  .step { position: absolute; display: flex; }
  .step-icon { width: 88px; height: 80px; background: var(--orange); display: flex; align-items: center; justify-content: center; }
  .step-text { margin-left: 19px; margin-top: 0; }
  .step-title { font-size: 19px; font-weight: 700; color: #333; line-height: 24px; }
  .step-desc { margin-top: 10px; font-size: 15px; line-height: 19px; color: #333; }

  .footer-rule { position: absolute; left: 132px; top: 817px; width: 936px; height: 5px; background: var(--rule); }
  .footer-legal { position: absolute; left: 132px; top: 858px; font-size: 15px; color: #333; }
  .footer-legal a { color: #333; text-decoration: none; }
  .footer-legal .sep { margin: 0 6px; }
  .social { position: absolute; left: 944px; top: 844px; display: flex; gap: 5px; list-style: none; }
  .social li { width: 38px; height: 38px; background: var(--orange); }
</style>
</head>
<body>
  <header class="site-header">
    <div class="brand">
      <span class="brand-mark"></span>
      <span class="brand-name">LoopVane</span>
    </div>
    <svg class="search-icon" width="20" height="20" viewBox="0 0 20 20" aria-label="Search">
      <circle cx="8" cy="8" r="6" fill="none" stroke="#333" stroke-width="1.4"/>
      <line x1="12.5" y1="12.5" x2="17" y2="17" stroke="#333" stroke-width="1.4"/>
    </svg>
    <ul class="main-nav">
      <li><a class="is-active" href="#">HOME</a></li>
      <li><a href="#">ABOUT</a></li>
      <li><a href="#">SIGN UP</a></li>
      <li><a href="#">SIGN IN</a></li>
      <li><a href="#">SUPPORT</a></li>
      <li><a href="#">CONTACT</a></li>
    </ul>
  </header>

  <section class="hero" role="img" aria-label="Illustration of a yellow taxi in a pale blue city skyline, linked by a dashed arc to hands holding a phone with a call button, with a cloud and a yellow sun">
    <h1 class="hero-title">Transportation network company</h1>
  </section>

  <p class="intro">Getting rides is fast, and it's easy. Simply complete&nbsp; the steps below&nbsp; and call from<br>any touch-tone phone to hail a ride at the best price!</p>

  <section class="steps">
    <div class="step" style="left:134px">
      <div class="step-icon">
        <svg width="56" height="48" viewBox="0 0 56 48" aria-hidden="true">
          <path d="M12 6 h32 l6 14 h2 a4 4 0 0 1 4 4 v12 h-56 v-12 a4 4 0 0 1 4-4 h2 z" fill="#fff"/>
          <path d="M15 10 h26 l4 10 h-34 z" fill="var(--orange)"/>
          <rect x="4" y="34" width="10" height="10" rx="2" fill="#fff"/>
          <rect x="42" y="34" width="10" height="10" rx="2" fill="#fff"/>
          <circle cx="10" cy="28" r="4" fill="var(--orange)"/>
          <circle cx="46" cy="28" r="4" fill="var(--orange)"/>
          <rect x="20" y="25" width="16" height="5" rx="2" fill="var(--orange)"/>
        </svg>
      </div>
      <div class="step-text">
        <h2 class="step-title">SIGN UP FOR FREE!</h2>
        <p class="step-desc">AND LINK YOUR ZARVIX OR<br>QUIRRA ACCOUNTS</p>
      </div>
    </div>
    <div class="step" style="left:458px">
      <div class="step-icon">
        <svg width="54" height="50" viewBox="0 0 54 50" aria-hidden="true">
          <circle cx="12" cy="10" r="6" fill="#fff"/>
          <circle cx="42" cy="10" r="6" fill="#fff"/>
          <path d="M2 32 a10 10 0 0 1 20-8 v8 z" fill="#fff"/>
          <path d="M52 32 a10 10 0 0 0-20-8 v8 z" fill="#fff"/>
          <circle cx="27" cy="19" r="9" fill="#fff" stroke="var(--orange)" stroke-width="2"/>
          <path d="M12 49 v-6 a15 13 0 0 1 30 0 v6 z" fill="#fff" stroke="var(--orange)" stroke-width="2"/>
        </svg>
      </div>
      <div class="step-text">
        <h2 class="step-title">ADD A NEW RIDER</h2>
        <p class="step-desc">AND LINK YOUR ZARVIX OR<br>QUIRRA ACCOUNTS</p>
      </div>
    </div>
    <div class="step" style="left:786px">
      <div class="step-icon">
        <svg width="44" height="44" viewBox="0 0 24 24" aria-hidden="true">
          <path fill="#fff" d="M6.6 10.8c1.4 2.8 3.8 5.1 6.6 6.6l2.2-2.2c.3-.3.7-.4 1-.2 1.1.4 2.3.6 3.6.6.6 0 1 .4 1 1V20c0 .6-.4 1-1 1C10.6 21 3 13.4 3 4c0-.6.4-1 1-1h3.5c.6 0 1 .4 1 1 0 1.3.2 2.5.6 3.6.1.3 0 .7-.2 1z"/>
        </svg>
      </div>
      <div class="step-text">
        <h2 class="step-title">CALL 555-014-7392</h2>
        <p class="step-desc">AND LINK YOUR ZARVIX OR<br>QUIRRA ACCOUNTS</p>
      </div>
    </div>
  </section>

  <div class="footer-rule"></div>
  <footer>
    <p class="footer-legal">© 2017 LoopVane.&nbsp;&nbsp; <a href="#">Terms of Use</a><span class="sep">|</span> <a href="#">Privacy</a></p>
    <ul class="social" aria-label="Social links">
      <li></li><li></li><li></li>
    </ul>
  </footer>
</body>
</html>
```